Website for Briar Hollow Gathering Church

Wordpress website design required for Briar Hollow Gathering Church. We are a family oriented church catering for age groups from school age to elderly people. The church has a wide variety of activities which it coordinates. The idea is to describe the activities on the activities page, but cross-link them to show which would be applicable to the different age groups.

We would like an inviting website which is easy to read and navigate.

Target Market(s)

Very wide audience - from school age youth to elderly people, so design and style should cater for both audiences.

Industry/Entity Type

Church

Coding

Coded - Design and coding required

Number of Pages Required

5+ page

Font styles to use
Sans Serif

Colors
0255a3
ffffff
0792cd
f78f20

Requirements
Must have
• Inviting website.
• Clear readable font.
• Space to import photos to balance text on each page.
• Need to project a dynamic and progressive feel for the church.
• Easy to navigate.
Nice to have
• Scrolling photos on pages. Ability to enter questions/ comments/prayer requests on Home page.
Should not have
• Conservative audience, so should not be too bold.

```html
<!DOCTYPE html>
<html lang="en">
<head>
<meta charset="utf-8">
<title>Briar Hollow Gathering Church</title>
<link href="https://fonts.googleapis.com/css2?family=Raleway:wght@400;500;600;700&family=Open+Sans:wght@400;600&display=swap" rel="stylesheet">
<style>
:root{
  --navy:#0255a3;
  --sky:#0792cd;
  --orange:#f78f20;
  --white:#ffffff;
  --ink:#333333;
  --muted:#555555;
  --footer:#0a4fa0;
}
*{margin:0;padding:0;box-sizing:border-box}
html,body{width:1200px;height:3125px;overflow:hidden}
body{font-family:"Open Sans",Arial,sans-serif;color:var(--ink);background:var(--white);position:relative}
.h{font-family:"Raleway",Arial,sans-serif;font-weight:500}
.abs{position:absolute}

/* header */
.site-header{position:absolute;left:0;top:0;width:1200px;height:125px;background:var(--white)}
.brand{left:162px;top:70px;display:flex;align-items:center;gap:8px;font-family:"Raleway",sans-serif;font-weight:600;font-size:19px;color:var(--navy)}
.brand-dot{width:14px;height:14px;border-radius:50%;background:var(--navy)}
.call{right:162px;top:30px;font-family:"Raleway",sans-serif;font-weight:700;font-size:15px;color:var(--ink);display:flex;align-items:center;gap:6px}
.call span{color:var(--orange)}
.nav{left:487px;top:82px;display:flex;gap:32px;font-family:"Raleway",sans-serif;font-weight:600;font-size:13px;color:var(--ink)}
.nav .active{color:var(--navy);position:relative}
.nav .active::after{content:"";position:absolute;left:0;right:0;bottom:-6px;height:2px;background:var(--orange)}

/* hero */
.hero{left:0;top:125px;width:1200px;height:548px;background:radial-gradient(ellipse at 50% 45%,#5b5246 0%,#3a342c 55%,#1f1c18 100%)}
.hero-title{left:0;top:180px;width:1200px;text-align:center;color:var(--white);font-size:50px;font-weight:400}
.hero-text{left:210px;top:258px;width:780px;text-align:center;color:var(--white);font-size:16px;line-height:28px}
.btn-ghost{left:539px;top:340px;width:122px;height:38px;border:2px solid var(--white);color:var(--white);font-family:"Raleway",sans-serif;font-weight:700;font-size:11px;display:flex;align-items:center;justify-content:center;gap:4px}
.arrow{top:258px;width:34px;height:34px;border:2px solid rgba(255,255,255,.8);border-radius:50%}

/* welcome */
.section-title{width:1200px;left:0;text-align:center;font-size:34px;color:var(--navy)}
.lead{left:200px;width:800px;text-align:center;color:var(--orange);font-size:14.5px;line-height:22px}
.body-copy{left:180px;width:840px;text-align:center;color:var(--muted);font-size:11px;line-height:20px}

/* activities */
.activities{left:0;top:975px;width:1200px;height:629px;background:radial-gradient(ellipse at 30% 20%,#8fb6cf 0%,#4f87aa 45%,#2f5f84 100%)}
.card{top:108px;width:277px;height:436px;background:var(--white)}
.card-photo{width:277px;height:220px}
.card h3{margin-top:22px;text-align:center;color:var(--navy);font-size:18px}
.card p{margin:12px 28px 0;text-align:center;font-size:11px;line-height:20px;color:var(--muted)}
.btn-outline{position:absolute;left:76px;top:375px;width:124px;height:36px;border:1px solid var(--orange);color:var(--orange);font-family:"Raleway",sans-serif;font-size:12px;display:flex;align-items:center;justify-content:center}

/* minister */
.minister{left:0;top:1604px;width:1200px;height:367px;background:radial-gradient(ellipse at 40% 40%,#8a4a3a 0%,#5c2826 50%,#34131a 100%)}
.minister h2{position:absolute;left:0;width:1200px;top:100px;text-align:center;color:var(--white);font-size:37px}
.minister p{position:absolute;left:255px;width:690px;top:168px;text-align:center;color:var(--white);font-size:14px;line-height:25px}

/* news */
.news-card{top:2063px;width:277px}
.news-photo{width:277px;height:169px}
.news-head{display:flex;gap:12px;align-items:flex-start}
.date{width:57px;height:58px;background:var(--sky);color:var(--white);text-align:center;font-family:"Raleway",sans-serif;line-height:1}
.date .m{display:block;font-size:13px;padding-top:7px}
.date .d{display:block;font-size:25px;font-weight:700;margin-top:3px}
.news-title{padding-top:10px;font-family:"Raleway",sans-serif;font-size:15px;line-height:20px;color:var(--navy);font-weight:500}
.news-card p{margin-top:14px;font-size:10.5px;line-height:19px;color:var(--muted)}

/* prayer */
.prayer{left:0;top:2423px;width:1200px;height:354px;background:radial-gradient(ellipse at 55% 40%,#8e7660 0%,#5e4a3e 50%,#3a2c2c 100%)}
.prayer h2{position:absolute;left:0;width:1200px;top:64px;text-align:center;color:var(--white);font-size:37px}
.prayer p{position:absolute;left:260px;width:680px;top:136px;text-align:center;color:var(--white);font-size:14px;line-height:25px}
.prayer-form{position:absolute;left:252px;top:204px;display:flex}
.field{width:598px;height:46px;background:var(--white);font-size:11px;color:var(--ink);padding:15px 12px}
.btn-solid{width:98px;height:46px;background:var(--orange);color:var(--white);font-family:"Raleway",sans-serif;font-weight:700;font-size:14px;display:flex;align-items:center;justify-content:center}

/* footer */
.site-footer{left:0;top:2777px;width:1200px;height:348px;background:var(--footer);color:var(--white)}
.fcol{top:44px}
.fcol h4{font-family:"Raleway",sans-serif;font-weight:700;font-size:15px;margin-bottom:12px}
.fcol li{list-style:none;font-size:11px;line-height:17.3px}
.times li{line-height:23px}
.contact-item{display:flex;gap:8px;font-size:11px;line-height:15px;margin-bottom:8px}
.contact-item svg{flex:none;margin-top:3px}
.fcol .small{font-size:11px;margin-bottom:10px}
.f-input{width:240px;height:34px;background:var(--white);color:#888;font-size:11px;font-style:italic;padding:10px 12px;margin-bottom:8px}
.f-row{display:flex}
.f-row .f-input{width:164px}
.f-row .btn-solid{width:76px;height:34px;font-size:13px}
.f-bottom{left:162px;top:279px;display:flex;align-items:center;gap:14px;font-size:11px;line-height:20px}
.f-mark{width:50px;height:50px;border-radius:50%;background:var(--white)}
.social-btn{left:835px;top:280px;width:205px;height:40px;background:#2d5ca8;border:1px solid #4a79c4;font-family:"Raleway",sans-serif;font-weight:600;font-size:15px;display:flex;align-items:center;justify-content:center}
</style>
</head>
<body>

<header class="site-header">
  <div class="abs brand"><span class="brand-dot"></span>Briar Hollow Gathering Church</div>
  <div class="abs call">
    <svg width="16" height="14" viewBox="0 0 16 14"><rect width="16" height="14" rx="2" fill="#f78f20"/><path d="M5 4c0 3 3 6 6 6l1-2-2-1-1 1c-1-.5-2-1.5-2.5-2.5l1-1-1-2z" fill="#fff"/></svg>
    CALL US: <span>555-014-2290</span>
  </div>
  <nav class="abs nav">
    <span class="active">Home</span><span>Age Group</span><span>Activites</span><span>Events Calendar</span><span>About BHGC</span><span>Contact</span>
  </nav>
</header>

<section class="abs hero" role="img" aria-label="Photo of the congregation gathered at tables in a courtyard">
  <h1 class="abs h hero-title">Briar Hollow Gathering Church</h1>
  <p class="abs hero-text">Sed ut perspiciatis unde omnis iste sit voluptatemccusantium doloremque laudantiumtot raSed ut perspiciatis unde omnis iste sit voluptatem accusantium doloremque.</p>
  <div class="abs btn-ghost">READ MORE
    <svg width="10" height="10" viewBox="0 0 10 10"><circle cx="5" cy="5" r="5" fill="#fff"/><path d="M4 2.5 6.5 5 4 7.5" stroke="#3a342c" stroke-width="1.5" fill="none"/></svg>
  </div>
  <svg class="abs arrow" style="left:40px" viewBox="0 0 34 34"><path d="M19 11l-6 6 6 6" stroke="#fff" stroke-width="2" fill="none"/></svg>
  <svg class="abs arrow" style="left:1118px" viewBox="0 0 34 34"><path d="M15 11l6 6-6 6" stroke="#fff" stroke-width="2" fill="none"/></svg>
</section>

<section>
  <h2 class="abs h section-title" style="top:715px">Welcome to Briar Hollow Gathering Church</h2>
  <p class="abs lead" style="top:778px">Sed ut perspiciatis unde omnis iste natus error sit voluptatem accusantium doloremque laudantium, totam rem aperiam, eaque ipsa quae ab illo inventore veritatis et quasi architecto beatae vitae dicta sunt explicabo.</p>
  <p class="abs body-copy" style="top:842px">Sed ut perspiciatis unde omnis iste natus error sit voluptatem accusantium doloremque laudantium, totam rem aperiam, eaque ipsa quae ab illo inventore veritatis et quasi architecto beatae vitae dicta sunt explicabo. Nemo enim ipsam voluptatem quia voluptas sit aspernatur aut odit aut fugit, sed quia consequuntur magni dolores eos qui Sed ut perspiciatis unde omnis iste natus error sit voluptatem accusantium doloremque laudantium, totam rem aperiam, eaque ipsa quae ab illo inventore veritatis et quasi architecto beatae vitae dicta sunt explicabo. Nemo enim ipsam voluptatem quia voluptas sit aspernatur aut odit aut fugit, sed quia consequuntur magni do.</p>
</section>

<section class="abs activities">
  <h2 class="abs h" style="left:0;width:1200px;top:36px;text-align:center;color:#fff;font-size:32px">Activity Areas</h2>
  <article class="abs card" style="left:162px">
    <div class="card-photo" role="img" aria-label="Photo of volunteers in the church kitchen" style="background:linear-gradient(135deg,#8a7a6a,#4e4238)"></div>
    <h3 class="h">Activity Area Name</h3>
    <p>Sd ut perspiciatis unde omnis iste natus or sit voluptatem accusantium doloremque laudan tium, totam rem aperiam, eaque ipsa quae ab illo inventore veritatis et quasi architect.</p>
    <div class="btn-outline">Read More</div>
  </article>
  <article class="abs card" style="left:462px">
    <div class="card-photo" role="img" aria-label="Photo of a shared meal in the church hall" style="background:linear-gradient(135deg,#6e6458,#2f2a26)"></div>
    <h3 class="h">Activity Area Name</h3>
    <p>Sd ut perspiciatis unde omnis iste natus or sit voluptatem accusantium doloremque laudan tium, totam rem aperiam, eaque ipsa quae ab illo inventore veritatis et quasi architect.</p>
    <div class="btn-outline">Read More</div>
  </article>
  <article class="abs card" style="left:762px">
    <div class="card-photo" role="img" aria-label="Photo of a garden gathering with tables of food" style="background:linear-gradient(135deg,#6f7a58,#3a3a2c)"></div>
    <h3 class="h">Activity Area Name</h3>
    <p>Sd ut perspiciatis unde omnis iste natus or sit voluptatem accusantium doloremque laudan tium, totam rem aperiam, eaque ipsa quae ab illo inventore veritatis et quasi architect.</p>
    <div class="btn-outline">Read More</div>
  </article>
</section>

<section class="abs minister" role="img" aria-label="Soft blurred background of warm candle lights">
  <h2 class="h">Minister's Weekly Message</h2>
  <p>Sed ut perspiciatis unde omnis iste natus error sit voluptatem accusantium doloremque laudan-tium, totam rem aperiam, eaque ipsa quae ab illo inventore veritatis et quasi architecto beatae vitae dicta sunt explicabo. Nemo enim ipsam voluptatem quia voluptas sit aspernatur</p>
</section>

<section>
  <h2 class="abs h section-title" style="top:2002px">News Summaries</h2>
  <article class="abs news-card" style="left:162px">
    <div class="news-photo" role="img" aria-label="Photo of members serving at a fundraising stall" style="background:linear-gradient(135deg,#8c7c6c,#4a3e36)"></div>
    <div class="news-head"><div class="date"><span class="m">OCT</span><span class="d">20</span></div><div class="news-title">Sed ut perspiciatis ndomis iste natus error sit olupt.</div></div>
    <p>Sd ut perspiciatis unde omnis isteiste natus error sit vo luptatem accusantium doloremque lloS ut perscliatis un de omnis isteiste natus Sed ut perspiciatis unde.</p>
  </article>
  <article class="abs news-card" style="left:462px">
    <div class="news-photo" role="img" aria-label="Photo of members chatting in the kitchen" style="background:linear-gradient(135deg,#7c7268,#3a3430)"></div>
    <div class="news-head"><div class="date"><span class="m">OCT</span><span class="d">20</span></div><div class="news-title">Sed ut perspiciatis ndomis iste natus error sit olupt.</div></div>
    <p>Sd ut perspiciatis unde omnis isteiste natus error sit vo luptatem accusantium doloremque lloS ut perscliatis un de omnis isteiste natus Sed ut perspiciati.</p>
  </article>
  <article class="abs news-card" style="left:762px">
    <div class="news-photo" role="img" aria-label="Photo of members at an outdoor garden event" style="background:linear-gradient(135deg,#5f7a4a,#3c3a2a)"></div>
    <div class="news-head"><div class="date"><span class="m">OCT</span><span class="d">20</span></div><div class="news-title">Sed ut perspiciatis ndomis iste natus error sit olupt.</div></div>
    <p>Sd ut perspiciatis unde omnis isteiste natus error sit vo luptatem accusantium doloremque lloS ut perscliatis un de omnis isteiste natus Sed ut perspiciati.</p>
  </article>
</section>

<section class="abs prayer" role="img" aria-label="Soft blurred background of warm evening lights">
  <h2 class="h">Area to Enter Prayer Request</h2>
  <p>Sed ut perspiciatis unde omnis iste natus error sit voluptatem accusantium doloremque lauda ntium, totam rem aperiam, eaque ipsa quae ab illo inventore veritatis et quasi archite.</p>
  <div class="prayer-form"><div class="field">E-mail address</div><div class="btn-solid">SIGN UP</div></div>
</section>

<footer class="abs site-footer">
  <div class="abs fcol" style="left:162px">
    <h4>Theme of Church</h4>
    <ul><li>Home</li><li>Who We Are</li><li>Covenant with First Peoples</li><li>Our Leaders</li><li>Safe Church</li><li>News</li><li>Administration</li><li>Contact Us</li></ul>
  </div>
  <div class="abs fcol times" style="left:373px">
    <h4>Service Times</h4>
    <ul><li>Mon- 7:00am to 6:00pm</li><li>Tue- 7:00am to 6:00pm</li><li>Wen- 7:00am to 6:00pm</li><li>Thu- 7:00am to 6:00pm</li><li>Fri- 7:00am to 6:00pm</li><li>Sun- 7:00am to 6:00pm</li></ul>
  </div>
  <div class="abs fcol" style="left:570px;width:200px">
    <h4>Contact Detail</h4>
    <div class="contact-item"><svg width="9" height="10" viewBox="0 0 9 10"><path d="M1 1l2-1 1.5 2.5-1 1c.5 1.5 1.5 2.5 3 3l1-1L10 7 9 9C4 9 1 5 1 1z" fill="#fff"/></svg><span>Phone: (08) 5550 4120<br>or 1300 555 418</span></div>
    <div class="contact-item"><svg width="9" height="11" viewBox="0 0 9 11"><path d="M4.5 0A4 4 0 0 0 .5 4c0 3 4 7 4 7s4-4 4-7a4 4 0 0 0-4-4z" fill="#fff"/><circle cx="4.5" cy="4" r="1.5" fill="#0a4fa0"/></svg><span>Postal Address: PO Box 417,<br>Briar Hollow WA 6901</span></div>
    <div class="contact-item"><svg width="9" height="11" viewBox="0 0 9 11"></svg><span>Physical Address: 12-16<br>Thornfield Rd, Briar Hollow</span></div>
    <div class="contact-item"><svg width="10" height="8" viewBox="0 0 10 8"><rect width="10" height="8" fill="#fff"/><path d="M0 0l5 4 5-4" stroke="#0a4fa0" fill="none"/></svg><span>office@briarhollowchurch.org</span></div>
  </div>
  <div class="abs fcol" style="left:795px">
    <h4>Form to Email Church</h4>
    <div class="small">Please sign up here for latest deals</div>
    <div class="f-input">Name:</div>
    <div class="f-row"><div class="f-input">Email address</div><div class="btn-solid">SIGN UP</div></div>
  </div>
  <div class="abs f-bottom"><span class="f-mark"></span><span>© 2016 Briar Hollow Gathering Church.<br>All Copyrights are reserved.Term of Use. Privacy Policy</span></div>
  <div class="abs social-btn">Login with Social</div>
</footer>

</body>
</html>
```